Kestal-Materials. Limestone; improving the world

New Limestone company and need logo design.
Limestone offsets carbon mitigation industries restore and replenish soil fertilities in the Prairies, the breadbasket of the world. At the same time, Limestone is proving a critical emergent component of carbon capture sequestration technology will therefore play a critical role in the development of the western Canadian energy industries
Our limestone resources are situated in the foothills of the Canadian Rockies well-positioned above the sprawling fields of the vast peace district.
Agriculture and oli sites
Kestal Materials
3 page

```html
<!DOCTYPE html>
<html lang="en">
<head>
<meta charset="utf-8">
<title>Kestal Materials</title>
<link rel="stylesheet" href="https://fonts.googleapis.com/css2?family=Gentium+Book+Plus:wght@400;700&family=Mulish:wght@500;600&display=swap">
<style>
  :root {
    --ink: #2f2925;
    --text: #3c3531;
    --green: #5cc13a;
    --white: #ffffff;
    --footer-bg: #f4f4f4;
    --copy: #e6f5de;
  }
  * { margin: 0; padding: 0; box-sizing: border-box; }
  html, body { width: 740px; height: 1200px; overflow: hidden; background: var(--white); }
  body { position: relative; font-family: "Gentium Book Plus", "Palatino Linotype", serif; color: var(--text); }
  .abs { position: absolute; }

  .site-header { position: absolute; left: 0; top: 0; width: 740px; height: 55px; background: var(--white); }
  .brand { left: 60px; top: 14px; display: flex; align-items: center; gap: 7px; font-size: 18px; color: var(--ink); }
  .brand-square { width: 18px; height: 18px; background: var(--ink); }
  .main-nav { left: 0; top: 25px; width: 740px; font-size: 9.6px; color: var(--ink); }
  .main-nav a { position: absolute; color: inherit; text-decoration: none; white-space: nowrap; }
  .main-nav .current { font-weight: 700; }

  .hero { left: 0; top: 55px; width: 740px; height: 317px;
    background: linear-gradient(180deg, #d9d6a3 0%, #c6b66a 30%, #8f8a4a 60%, #4e5030 100%); }
  .hero-glow { left: 0; top: 55px; width: 740px; height: 317px;
    background: radial-gradient(ellipse 260px 140px at 540px 10px, rgba(255,244,190,.85), rgba(255,240,170,0) 70%); }
  .hero-title { left: 40px; top: 300px; width: 660px; text-align: center; font-family: "Mulish", sans-serif; font-weight: 500;
    font-size: 16.5px; line-height: 29.5px; color: var(--white); }

  .mission { left: 63px; top: 410px; width: 320px; font-size: 19px; line-height: 27px; color: var(--text); }
  .mission strong { color: var(--ink); }

  .section-title { font-weight: 700; color: var(--green); font-size: 17.5px; line-height: 22px; }
  .body-copy { font-size: 10.2px; line-height: 17px; color: var(--text); }

  .about { left: 412px; top: 413px; width: 272px; }
  .about .body-copy { margin-top: 5px; }
  .opportunities { left: 412px; top: 539px; width: 272px; }
  .opportunities .body-copy { margin-top: 6px; }

  .features { left: 62px; top: 695px; width: 300px; }
  .features .body-copy { margin-top: 5px; }
  .feature-list { list-style: none; margin-top: 8px; }
  .feature-list li { border-left: 2px solid var(--ink); padding-left: 5px; font-size: 10.2px; line-height: 17px; margin-bottom: 6px; }
  .cta { display: inline-block; margin-top: 3px; background: var(--green); color: var(--white); font-size: 11.6px;
    line-height: 26px; padding: 0 8px; text-decoration: none; }

  .fields-photo { left: 381px; top: 676px; width: 298px; height: 268px;
    background: linear-gradient(180deg, #8fa9cf 0%, #c9d3e0 30%, #5d5a3a 36%, #5b7a3a 55%, #4f8a34 100%); }

  .site-footer { left: 0; top: 1020px; width: 740px; height: 147px; background: var(--footer-bg); }
  .footer-contact { left: 62px; top: 1043px; font-size: 10.2px; line-height: 15px; color: var(--ink); }
  .footer-contact .company { font-weight: 700; font-size: 11.6px; margin-bottom: 6px; }
  .footer-contact .inquiry { margin-top: 26px; }
  .footer-nav { left: 413px; top: 1043px; font-size: 9.6px; line-height: 18.6px; }
  .footer-nav a { display: block; color: var(--ink); text-decoration: none; }
  .footer-nav .current { font-weight: 700; }

  .copyright-bar { left: 0; top: 1167px; width: 740px; height: 33px; background: var(--green);
    text-align: center; font-size: 9.6px; line-height: 33px; color: var(--copy); }
</style>
</head>
<body>
  <header class="site-header">
    <div class="abs brand"><span class="brand-square"></span><span>Kestal Materials</span></div>
    <nav class="abs main-nav">
      <a class="current" style="left:440px">Home</a>
      <a style="left:500px">About Us</a>
      <a style="left:573px">FAQs</a>
      <a style="left:631px">Contact Us</a>
    </nav>
  </header>

  <div class="abs hero" role="img" aria-label="Aerial photo of a truck on a highway beside a warehouse and prairie fields at sunrise"></div>
  <div class="abs hero-glow"></div>
  <h1 class="abs hero-title">Limestone Offsets Carbon Mitigation Industries Restore And Replenish Soil Fertilities In The Prairies, The Breadbasket of The World.</h1>

  <p class="abs mission"><strong>Our Mission</strong>&nbsp; Is to Improve our world by responsibly meeting society’s needs for quality lime and limestone products.</p>

  <section class="abs about">
    <h2 class="section-title">About Us</h2>
    <p class="body-copy">Lorem ipsum dolor sit amet, consectetuer adpiscing elit, sed diam nonummy nibh euismod tincidunt ut laoreet dolore magna aliquam erat volutpat. Ut wisi enim ad minim veniam, quis nostrud exerci tatiofdn ullamcorper suscipit lobortis nisl ut aliquip commodo.</p>
  </section>

  <section class="abs opportunities">
    <h2 class="section-title">Special Opportunities</h2>
    <p class="body-copy">Our limestone resources are situated in the foothills of the Canadian Rockies well-positioned above the sprawling fields of the vast peace district.</p>
  </section>

  <section class="abs features">
    <h2 class="section-title">Loreem Ipsum Dolor</h2>
    <p class="body-copy">Lorem ipsum dolor sit amet, contetr adpiscing elit, sed diam nonummy nibh eumod tincidunt.</p>
    <ul class="feature-list">
      <li>Lorem ipsum dolor sit amet, contetr adpiscing elit</li>
      <li>Ased diam nonummy nibh eumod tincidunt ut laoreet dolore magna aliquam erat volutpat.</li>
      <li>Lorem ipsum dolor sit amet, contetr adpiscing elit</li>
      <li>Ased diam nonummy nibh eumod tincidunt ut laoreet dolore magna aliquam erat volutpat.</li>
    </ul>
    <a class="cta">Contact Us Today</a>
  </section>

  <div class="abs fields-photo" role="img" aria-label="Aerial photo of green prairie fields with hay bales under a cloudy sky"></div>

  <footer class="abs site-footer"></footer>
  <div class="abs footer-contact">
    <p class="company">Kestal-Materials Management, LLC</p>
    <p>512 Orchard Ave, 9th Floor<br>Denver, CO 80202</p>
    <p class="inquiry">For any inquiries, please contact<br>hello@kestalmaterials.com</p>
  </div>
  <nav class="abs footer-nav">
    <a class="current">Home</a>
    <a>About Us</a>
    <a>FAQs</a>
    <a>Contact Us</a>
  </nav>
  <div class="abs copyright-bar">Copyright © 2021 Kestal-Materials.&nbsp; All Right Reserved.</div>
</body>
</html>
```